Brivane Management

We need a web design for a new consulting company, with clients all over the world. The company provides management consulting to the travel industry.

Logo files are attached.

Website must look very corporate and be responsive in design.

Management Consulting

```html
<!DOCTYPE html>
<html lang="en">
<head>
<meta charset="utf-8">
<title>Brivane Management</title>
<link href="https://fonts.googleapis.com/css2?family=Open+Sans:wght@400;600;700;800&display=swap" rel="stylesheet">
<style>
:root{
  --blue:#1c5d9c;
  --blue-dark:#143f6b;
  --green:#78b13a;
  --text:#555;
  --light:#f1f1f1;
  --grey:#e4e4e4;
  --line:#d6d6d6;
  --footer:#2f3236;
  --footer-dark:#23262a;
  --white:#fff;
}
*{box-sizing:border-box;margin:0;padding:0}
html,body{width:882px;height:1200px;overflow:hidden}
body{font-family:"Open Sans",Arial,sans-serif;color:var(--text);background:var(--white);font-size:9px;line-height:1.45}
.page{width:882px;height:1200px;position:relative}

/* header */
.site-header{height:68px;display:flex;justify-content:space-between;align-items:flex-start;padding:10px 100px 0 100px}
.brand{display:flex;align-items:center;gap:8px;margin-top:6px}
.brand-mark{width:30px;height:30px;border-radius:50%;background:var(--green)}
.brand-name{font-weight:800;font-size:19px;color:var(--blue);letter-spacing:.5px}
.header-right{display:flex;flex-direction:column;align-items:flex-end;gap:6px}
.phone{display:flex;align-items:center;gap:5px;font-size:12px;color:#333;font-weight:600}
.main-nav{display:flex;border:1px solid var(--line)}
.main-nav a{padding:6px 12px;font-size:10px;color:#444;text-decoration:none;border-left:1px solid var(--line)}
.main-nav a:first-child{border-left:none;color:var(--blue);font-weight:600}

/* hero */
.hero{position:relative;height:262px;background:linear-gradient(180deg,#5d6e82 0%,#a8a79b 45%,#c9a97a 65%,#6d5a3f 82%,#3b3226 100%)}
.hero-caption{position:absolute;left:0;right:0;bottom:0;height:30px;background:rgba(0,0,0,.45);color:var(--white);text-align:center;font-size:15px;font-weight:600;line-height:30px;letter-spacing:.3px}
.hero-arrow{position:absolute;top:112px;width:22px;height:22px;border-radius:50%;background:rgba(0,0,0,.6);display:flex;align-items:center;justify-content:center}
.hero-arrow.prev{left:80px}.hero-arrow.next{right:80px}

/* section headings */
.section-title{text-align:center;font-size:15px;font-weight:800;color:var(--blue);letter-spacing:.5px}
.section-title span{color:var(--green)}

/* about */
.about{height:130px;padding:12px 100px 0}
.about-heading{display:flex;justify-content:center;align-items:center;gap:8px;margin-bottom:8px}
.about-heading .title{font-size:15px;font-weight:800;color:var(--blue)}
.about-heading .brand-mark{width:20px;height:20px}
.about-heading .name{font-size:14px;font-weight:800;color:var(--blue)}
.about p{margin-bottom:6px;font-size:8.5px;color:#666}

/* services */
.services{height:148px;background:var(--light);border-top:1px solid var(--grey);border-bottom:1px solid var(--grey);padding-top:10px}
.service-list{display:flex;justify-content:center;gap:40px;margin-top:14px}
.service{width:92px;text-align:center}
.service-icon{width:44px;height:44px;border-radius:50%;background:var(--white);border:2px solid var(--line);margin:0 auto 6px;display:flex;align-items:center;justify-content:center}
.service-name{font-size:7.5px;font-weight:700;color:#333;line-height:1.3}

/* three columns */
.info{display:flex;gap:20px;padding:14px 100px 0;height:188px}
.info-col{flex:1}
.col-title{display:flex;align-items:center;gap:5px;font-size:12px;font-weight:800;color:var(--blue);border-bottom:1px solid var(--line);padding-bottom:4px;margin-bottom:8px}
.col-title span{color:var(--green)}
.news-item{margin-bottom:8px;font-size:7.5px;color:#666}
.news-date{font-weight:700;color:#333}
.read-more{display:block;text-align:right;color:var(--blue);font-size:7.5px}
.quote{background:var(--light);border:1px solid var(--grey);padding:8px;font-size:7.5px;color:#666;font-style:normal}
.author{display:flex;align-items:center;gap:6px;margin-top:8px;font-size:8px;font-weight:700;color:#333}
.author-photo{width:26px;height:26px;background:#9aa4ae}
.form-field{display:flex;align-items:center;margin-bottom:5px;font-size:7.5px}
.form-field label{width:34px}
.form-field .input{flex:1;height:14px;border:1px solid var(--line)}
.form-field .input.tall{height:34px}
.submit{margin-left:34px;background:var(--blue);color:var(--white);font-size:7.5px;padding:2px 10px;display:inline-block}

/* clients */
.clients{height:174px;padding-top:8px}
.client-row{display:flex;align-items:center;justify-content:center;gap:14px;margin-top:18px}
.client{width:96px;height:44px;border:1px solid var(--grey);display:flex;align-items:center;justify-content:center;font-size:12px;font-weight:700;color:#444}
.client-arrow{width:18px;height:18px;border-radius:50%;background:#555;display:flex;align-items:center;justify-content:center}

/* footer */
.site-footer{position:absolute;left:0;right:0;bottom:0;height:225px;background:var(--footer);color:#ccc}
.footer-top{display:flex;padding:16px 100px 0;gap:18px;height:180px}
.footer-block h4{color:var(--white);font-size:8.5px;font-weight:700;margin-bottom:6px}
.subscribe{width:150px}
.subscribe-box{display:flex}
.subscribe-box .input{flex:1;height:14px;background:var(--white)}
.subscribe-box .go{width:18px;height:14px;background:var(--blue)}
.contact-lines{font-size:7.5px;line-height:1.6}
.social{display:flex;gap:4px}
.social i{display:block;width:14px;height:14px;background:var(--blue)}
.footer-brand{margin-left:auto;display:flex;align-items:center;gap:8px}
.footer-brand .brand-mark{width:32px;height:32px}
.footer-brand .brand-name{color:var(--white);font-size:20px}
.footer-bottom{height:45px;background:var(--footer-dark);display:flex;justify-content:space-between;align-items:center;padding:0 100px;font-size:7.5px;color:#aaa}
</style>
</head>
<body>
<div class="page">

  <header class="site-header">
    <div class="brand"><span class="brand-mark"></span><span class="brand-name">BRIVANE MANAGEMENT</span></div>
    <div class="header-right">
      <div class="phone">
        <svg width="12" height="12" viewBox="0 0 24 24"><path fill="#1c5d9c" d="M6.6 10.8c1.4 2.8 3.8 5.1 6.6 6.6l2.2-2.2c.3-.3.7-.4 1-.2 1.1.4 2.3.6 3.6.6.6 0 1 .4 1 1V20c0 .6-.4 1-1 1C10.6 21 3 13.4 3 4c0-.6.4-1 1-1h3.5c.6 0 1 .4 1 1 0 1.3.2 2.5.6 3.6.1.3 0 .7-.2 1z"/></svg>
        555 014 2290
      </div>
      <nav class="main-nav"><a>Home</a><a>About Us</a><a>Services</a><a>Contact Us</a></nav>
    </div>
  </header>

  <section class="hero" role="img" aria-label="Photograph of an elephant walking across a savanna at sunset">
    <span class="hero-arrow prev"><svg width="8" height="8" viewBox="0 0 8 8"><path d="M6 0L2 4l4 4" stroke="#fff" stroke-width="1.6" fill="none"/></svg></span>
    <span class="hero-arrow next"><svg width="8" height="8" viewBox="0 0 8 8"><path d="M2 0l4 4-4 4" stroke="#fff" stroke-width="1.6" fill="none"/></svg></span>
    <div class="hero-caption">WE PROVIDE A CUSTOMIZED PLAN FOR FINANCIAL IMPROVEMENT</div>
  </section>

  <section class="about">
    <div class="about-heading"><span class="title">ABOUT</span><span class="brand-mark"></span><span class="name">BRIVANE</span></div>
    <p>Lorem ipsum dolor sit amet, consectetuer adipiscing elit. Sed diam nonummy nibh euismod tincidunt ut laoreet dolore magna aliquam erat volutpat. Ut wisi enim ad minim veniam, quis nostrud exerci tation ullamcorper suscipit lobortis nisl ut aliquip ex ea commodo consequat. Duis autem vel eum iriure dolor in hendrerit in vulputate velit esse molestie consequat.</p>
    <p>Vel illum dolore eu feugiat nulla facilisis at vero eros et accumsan et iusto odio dignissim qui blandit praesent luptatum zzril delenit augue duis dolore.</p>
  </section>

  <section class="services">
    <h2 class="section-title"><span>OUR</span> SERVICES</h2>
    <div class="service-list">
      <div class="service"><div class="service-icon"><svg width="24" height="24" viewBox="0 0 24 24"><rect x="3" y="14" width="4" height="7" fill="#1c5d9c"/><rect x="10" y="10" width="4" height="11" fill="#1c5d9c"/><rect x="17" y="6" width="4" height="15" fill="#1c5d9c"/><path d="M3 11L11 5l3 3 7-6" stroke="#78b13a" stroke-width="2" fill="none"/></svg></div><div class="service-name">SALES/<br>MARKETING</div></div>
      <div class="service"><div class="service-icon"><svg width="24" height="24" viewBox="0 0 24 24"><circle cx="12" cy="12" r="9" stroke="#1c5d9c" stroke-width="2" fill="none"/><circle cx="12" cy="12" r="5" stroke="#78b13a" stroke-width="2" fill="none"/><circle cx="12" cy="12" r="1.5" fill="#1c5d9c"/></svg></div><div class="service-name">STRATEGIC<br>PLANNING</div></div>
      <div class="service"><div class="service-icon"><svg width="24" height="24" viewBox="0 0 24 24"><circle cx="12" cy="12" r="9" fill="#1c5d9c"/><path d="M15 8.5c-.6-.9-1.7-1.4-3-1.4-1.7 0-3 .9-3 2.2 0 3 6 1.6 6 4.7 0 1.3-1.3 2.3-3 2.3-1.4 0-2.6-.6-3.2-1.6M12 5.5v13" stroke="#fff" stroke-width="1.6" fill="none"/></svg></div><div class="service-name">HUMAN CAPITAL<br>MANAGEMENT SOLUTIONS</div></div>
      <div class="service"><div class="service-icon"><svg width="24" height="24" viewBox="0 0 24 24"><rect x="3" y="4" width="18" height="12" stroke="#1c5d9c" stroke-width="2" fill="none"/><path d="M9 20h6M12 16v4" stroke="#1c5d9c" stroke-width="2"/><path d="M6 13l4-4 3 2 4-5" stroke="#78b13a" stroke-width="1.6" fill="none"/></svg></div><div class="service-name">FINANCIAL<br>ANALYSIS</div></div>
      <div class="service"><div class="service-icon"><svg width="24" height="24" viewBox="0 0 24 24"><ellipse cx="12" cy="7" rx="7" ry="3" fill="#78b13a"/><path d="M5 7v5c0 1.7 3.1 3 7 3s7-1.3 7-3V7" stroke="#1c5d9c" stroke-width="1.6" fill="none"/><path d="M5 12v5c0 1.7 3.1 3 7 3s7-1.3 7-3v-5" stroke="#1c5d9c" stroke-width="1.6" fill="none"/></svg></div><div class="service-name">CASH MANAGEMENT<br>SOLUTIONS</div></div>
    </div>
  </section>

  <section class="info">
    <div class="info-col">
      <h3 class="col-title"><svg width="10" height="10" viewBox="0 0 10 10"><rect width="10" height="10" fill="#1c5d9c"/></svg><span>LATEST</span> NEWS</h3>
      <div class="news-item"><div class="news-date">09/10/2014</div>Lorem ipsum dolor sit amet, consectetuer adipiscing elit, sed diam nonummy nibh euismod tincidunt ut laoreet.<a class="read-more">Read more »</a></div>
      <div class="news-item"><div class="news-date">09/10/2014</div>Lorem ipsum dolor sit amet, consectetuer adipiscing elit, sed diam nonummy nibh euismod tincidunt ut laoreet.<a class="read-more">Read more »</a></div>
    </div>
    <div class="info-col">
      <h3 class="col-title"><svg width="10" height="10" viewBox="0 0 10 10"><circle cx="5" cy="5" r="5" fill="#1c5d9c"/></svg><span>CLIENT</span> TESTIMONIAL</h3>
      <blockquote class="quote">Duis autem vel eum iriure dolor in hendrerit in vulputate velit esse molestie consequat, vel illum dolore eu feugiat nulla facilisis at vero eros et accumsan.</blockquote>
      <div class="author"><span class="author-photo" role="img" aria-label="Client portrait"></span>Mr. Daniel K. Merrow</div>
    </div>
    <div class="info-col">
      <h3 class="col-title"><svg width="10" height="10" viewBox="0 0 10 10"><rect y="2" width="10" height="7" fill="#1c5d9c"/></svg><span>QUICK</span> CONTACT</h3>
      <div class="form-field"><label>Name</label><span class="input"></span></div>
      <div class="form-field"><label>Email</label><span class="input"></span></div>
      <div class="form-field"><label>Message</label><span class="input tall"></span></div>
      <span class="submit">Submit</span>
    </div>
  </section>

  <section class="clients">
    <h2 class="section-title"><span>OUR</span> CLIENTS</h2>
    <div class="client-row">
      <span class="client-arrow"><svg width="8" height="8" viewBox="0 0 8 8"><path d="M6 0L2 4l4 4" stroke="#fff" stroke-width="1.6" fill="none"/></svg></span>
      <div class="client">Norvale</div>
      <div class="client">Tessline</div>
      <div class="client">Quillmark</div>
      <div class="client">Ambrecht</div>
      <div class="client">Ledgerly</div>
      <span class="client-arrow"><svg width="8" height="8" viewBox="0 0 8 8"><path d="M2 0l4 4-4 4" stroke="#fff" stroke-width="1.6" fill="none"/></svg></span>
    </div>
  </section>

  <footer class="site-footer">
    <div class="footer-top">
      <div class="footer-block subscribe"><h4>Subscribe to Newsletter</h4><div class="subscribe-box"><span class="input"></span><span class="go"></span></div></div>
      <div class="footer-block"><h4>Contact Us</h4><div class="contact-lines">555 014 2290<br>info@brivane.example</div></div>
      <div class="footer-block"><h4>Follow Us</h4><div class="social"><i></i><i></i><i></i></div></div>
      <div class="footer-brand"><span class="brand-mark"></span><span class="brand-name">BRIVANE MANAGEMENT</span></div>
    </div>
    <div class="footer-bottom"><span>Home | About Us | Services | Contact Us | Terms Conditions</span><span>© 2014 Brivane Management. All Rights Reserved</span></div>
  </footer>

</div>
</body>
</html>
```